Public Relations Agency Seeks Wordpress Design and Coding

TRELVOX Studio is a public relations agency specializing in media relations, public affairs and marketing communication.

The site should display the following visual characteristics: professionalism, trustworthiness, high-tech focus, clear and concise design.

The desired colors are royal blue, gray and hints of red.

Design look/feel inspired by this site: http://brightpathgatherings.example/

Specifications:

1. Navigation/Pages/Index:

HOME

ABOUT US

SERVICES

NEWS

CONTACT

---

2. Functionality of/content for each page:

- Home
o Dominant photo (professional, edgy, innovative)
o Simple, straightforward access to/from “Home” from other pages
o Includes logo (attached) and tagline "Unleash the power of communication"
o Direct link to “CONTACT”
o Links to social media accounts: Facebook, Chirpline, LinkedIn

- About Us

o Company profile blurb
o President’s photo with short bio

- Services
o Public Relations
 Strategic communication
 Brand and reputation management
 Community relations
o Media Relations
 News coverage and contacts
 Media training and interview skills
 Crisis communications
o Congressional Affairs
 Public affairs
 Public policy
 Legislative strategy
o Mass Communication
 Speechwriting
 Presentation creation
 Social media
o Marketing Communications
 Business collateral material
 Promotional campaigns
 Special events and tradeshows

- News
o Blog-like page to post information and/or share news from other sites

- Contact
o Standard “Contact Us” form (Name, Email, Phone, Message)
o Direct Contact
 (407) 555-0164
 Marisol@TRELVOXstudio.example

Target Market(s)

Small to large businesses specializing in high technology, defense/military, medicine/healthcare, and wide array of professional services.

Industry/Entity Type

Marketing

Font styles to use
Serif
Sans Serif

Colors
0555a3
ec2027
edf3f7

Requirements
Must have
• -- Project reqires DESIGN - and - fully CODED.

-- Strong SEO

-- Optimized for mobile viewing

Thank you!

```html
<!DOCTYPE html>
<html lang="en">
<head>
<meta charset="utf-8">
<title>TRELVOX Studio — Public Relations Agency</title>
<link href="https://fonts.googleapis.com/css2?family=Arimo:wght@400;700&display=swap" rel="stylesheet">
<style>
:root{
  --blue:#0555a3;
  --red:#ec2027;
  --pale:#edf3f7;
  --grey-bg:#f2f2f2;
  --text:#555;
  --dark:#2b2b2b;
  --darker:#1e1e1e;
  --white:#fff;
}
*{margin:0;padding:0;box-sizing:border-box}
html,body{width:1200px;height:2782px;overflow:hidden}
body{font-family:"Arimo",Arial,sans-serif;color:var(--text);background:var(--white);position:relative}
a{text-decoration:none}
section,header,footer,div{position:relative}
.btn{position:absolute;background:var(--red);color:var(--white);font-size:14px;display:flex;align-items:center;justify-content:center;border-radius:2px;text-decoration:none}

/* top bar */
.topbar{height:41px;background:var(--blue);color:var(--white);font-size:13px}
.topbar .phone{position:absolute;left:810px;top:12px;display:flex;gap:8px;align-items:center}
.topbar .social{position:absolute;left:990px;top:12px;display:flex;gap:12px}
.topbar .social span{width:13px;height:15px;border:2px solid var(--white);border-radius:2px;display:block}

/* header */
.site-header{height:126px}
.brand{position:absolute;left:141px;top:44px;display:flex;align-items:center;gap:10px;font-size:30px;color:#555;font-weight:700;letter-spacing:1px}
.brand i{width:11px;height:11px;background:var(--red);display:block}
.nav{position:absolute;top:49px;left:598px;display:flex;align-items:center;font-size:13px;color:#222}
.nav a{color:#222;display:flex;align-items:center;gap:6px}
.nav .active{background:var(--red);color:var(--white);width:64px;height:30px;justify-content:center;margin-right:34px}
.nav .item{margin-right:24px}
.nav .item::after{content:"";border:4px solid transparent;border-top:5px solid var(--red);margin-top:5px}

/* hero */
.hero{height:482px;background:linear-gradient(100deg,#2b3442 0%,#4a5d77 35%,#6c86a4 55%,#3d4a5c 80%,#1f2630 100%)}
.hero h1{position:absolute;top:190px;width:100%;text-align:center;color:var(--white);font-weight:400;font-size:42px}
.hero .btn{left:525px;top:276px;width:148px;height:52px;font-size:21px}
.hero .dots{position:absolute;top:405px;left:574px;display:flex;gap:6px}
.hero .dots span{width:12px;height:12px;border-radius:50%;background:var(--white)}
.hero .dots span:first-child{background:var(--red)}

/* welcome */
.welcome{height:366px}
.portrait{position:absolute;left:141px;top:58px;width:315px;height:252px;background:linear-gradient(90deg,#8a4a4a,#c7b9a9 45%,#b23030)}
.welcome h2{position:absolute;left:493px;top:54px;color:var(--blue);font-weight:400;font-size:28px}
.welcome p{position:absolute;left:493px;top:100px;width:565px;font-size:12px;line-height:24.5px;color:#777}
.welcome .btn{left:493px;top:270px;width:116px;height:40px}

/* services */
.services{height:450px;background:linear-gradient(120deg,#e04a4a,#d83a3c 50%,#e35752)}
.card{position:absolute;top:29px;width:294px;height:390px;background:var(--white);text-align:center}
.card .icon{position:absolute;left:71px;top:28px;width:152px;height:152px;border-radius:50%;background:var(--blue);display:flex;align-items:center;justify-content:center}
.card h3{position:absolute;top:210px;width:100%;font-weight:400;font-size:17px;color:#222}
.card p{position:absolute;top:244px;left:20px;right:20px;font-size:12px;line-height:20.5px;color:#666}
.card .btn{left:86px;top:323px;width:122px;height:38px}

/* news */
.news{height:334px;background:var(--grey-bg)}
.news h2{position:absolute;left:141px;top:32px;color:var(--blue);font-weight:400;font-size:30px}
.story .thumb{position:absolute;top:93px;width:216px;height:186px}
.story h3{position:absolute;top:88px;font-weight:400;font-size:17px;color:#222}
.story p{position:absolute;top:125px;width:210px;font-size:12px;line-height:20.5px;color:#555}
.story time{position:absolute;top:207px;font-size:12px;color:var(--red)}
.story .btn{top:240px;width:84px;height:38px;font-size:13px}

/* partners */
.partners{height:310px}
.badge{position:absolute;top:42px;width:92px;height:100px;background:#cfcfcf;border-radius:50%}
.partners h3{position:absolute;top:180px;width:100%;text-align:center;font-weight:400;font-size:17px;color:#222}
.partners .rule{position:absolute;left:195px;top:212px;width:806px;height:4px;background:#ddd}
.partners p{position:absolute;left:190px;top:228px;width:820px;text-align:center;font-size:12px;line-height:22px;color:#888}

/* contact */
.contact{height:358px;background:var(--blue);color:var(--white)}
.contact h2{position:absolute;top:32px;width:100%;text-align:center;font-weight:400;font-size:30px;display:flex;justify-content:center;align-items:center;gap:14px}
.field{position:absolute;left:141px;width:412px;height:43px;background:var(--white);color:#777;font-size:13px;padding:13px 14px}
.field.message{left:579px;top:108px;width:478px;height:172px}
.contact .note{position:absolute;left:141px;top:308px;font-size:13.5px}

/* footer */
.site-footer{height:228px;background:var(--dark);color:#ddd}
.col{position:absolute;top:38px}
.col h4{font-weight:400;font-size:14px;color:var(--white);margin-bottom:24px}
.col li{list-style:none;font-size:11.5px;line-height:20.5px}
.follow li{display:flex;align-items:center;gap:12px;margin-bottom:12px}
.follow li span{width:28px;height:28px;background:var(--blue);display:block}
.follow li:last-child span{background:#e8872c}
.bottombar{height:87px;background:var(--darker);color:#888;font-size:11px}
.bottombar .mark{position:absolute;left:141px;top:28px;font-size:22px;font-weight:700;color:#777}
.bottombar .links{position:absolute;left:294px;top:38px}
.bottombar .copy{position:absolute;left:795px;top:35px;color:#666}
</style>
</head>
<body>

<div class="topbar">
  <div class="phone">
    <svg width="10" height="16" viewBox="0 0 10 16"><rect x="1" y="1" width="8" height="14" rx="1.5" fill="none" stroke="#fff" stroke-width="1.6"/><circle cx="5" cy="12.5" r="1" fill="#fff"/></svg>
    +111 000 000
  </div>
  <div class="social"><span></span><span></span><span></span></div>
</div>

<header class="site-header">
  <div class="brand">TRELVOX Studio<i></i></div>
  <nav class="nav">
    <a class="active" href="#">Home</a>
    <a class="item" href="#">About us</a>
    <a class="item" href="#">Services</a>
    <a class="item" href="#">News</a>
    <a class="item" href="#">Contact us</a>
  </nav>
</header>

<section class="hero" role="img" aria-label="Hands pointing at a digital marketing screen">
  <h1>" Unleash the power of communication "</h1>
  <a class="btn" href="#">VIEW MORE</a>
  <div class="dots"><span></span><span></span><span></span></div>
</section>

<section class="welcome">
  <div class="portrait" role="img" aria-label="Portrait of the agency president"></div>
  <h2>WELCOME TO OUR AGENCY</h2>
  <p>Lorem Ipsum is simply dummy text of the printing and typesetting industry. Lorem Ipsum has been the industry's standard dummy text ever since the t is a long established fact that a reader will be distracted by the readable content of a page when looking at its layout. The point of using Lorem Ipsum is that it has a more-or-less normal distribution of letters, as opposed to using 'Content here, content here It is a long established fact that a reader will be distracted by the Content here, content here It is a long established fact that a reader will be distracted by the......</p>
  <a class="btn" href="#">Read More</a>
</section>

<section class="services">
  <div class="card" style="left:141px">
    <div class="icon"><svg width="50" height="66" viewBox="0 0 50 66"><rect x="15" y="2" width="20" height="36" rx="10" fill="#fff"/><path d="M6 28 Q6 48 25 48 Q44 48 44 28" fill="none" stroke="#fff" stroke-width="4"/><line x1="25" y1="48" x2="25" y2="60" stroke="#fff" stroke-width="4"/><line x1="14" y1="62" x2="36" y2="62" stroke="#fff" stroke-width="4"/></svg></div>
    <h3>MEDIA RELATIONS</h3>
    <p>reader will be distracted by the readable content of a page when looking at its layout. The point of using Lorem Ipsum</p>
    <a class="btn" href="#">Read More</a>
  </div>
  <div class="card" style="left:454px">
    <div class="icon"><svg width="84" height="60" viewBox="0 0 84 60"><path d="M4 22 L22 10 L40 16 L58 10 L80 22 L60 44 Q54 50 48 44 L38 36 L28 46 Q22 50 18 44 Z" fill="#fff"/><path d="M34 22 L46 34" stroke="#0555a3" stroke-width="3"/></svg></div>
    <h3>PUBLIC AFFAIRS</h3>
    <p>reader will be distracted by the readable content of a page when looking at its layout. The point of using Lorem Ipsum</p>
    <a class="btn" href="#">Read More</a>
  </div>
  <div class="card" style="left:764px">
    <div class="icon"><svg width="60" height="60" viewBox="0 0 60 60"><line x1="44" y1="12" x2="14" y2="30" stroke="#fff" stroke-width="5"/><line x1="14" y1="30" x2="44" y2="48" stroke="#fff" stroke-width="5"/><circle cx="44" cy="12" r="9" fill="#fff"/><circle cx="14" cy="30" r="9" fill="#fff"/><circle cx="44" cy="48" r="9" fill="#fff"/></svg></div>
    <h3>MARKETING COMMUNICATION</h3>
    <p>reader will be distracted by the readable content of a page when looking at its layout. The point of using Lorem Ipsum</p>
    <a class="btn" href="#">Read More</a>
  </div>
</section>

<section class="news">
  <h2>OUR LATEST NEWS</h2>
  <article class="story">
    <div class="thumb" role="img" aria-label="Group of officials at an outdoor event" style="left:141px;background:linear-gradient(120deg,#6f8a9e,#a4b36a 50%,#4a5668)"></div>
    <h3 style="left:377px">LOREM IPSUM IS SIMPLY</h3>
    <p style="left:377px">Lorem Ipsum is simply dummy text of the printing and typesetting industry. Lorem Ipsum has been the</p>
    <time style="left:377px">MARCH 14, 2013</time>
    <a class="btn" href="#" style="left:377px">Read More</a>
  </article>
  <article class="story">
    <div class="thumb" role="img" aria-label="Office team working with headsets at computers" style="left:621px;background:linear-gradient(120deg,#d9d9d9,#3a3a3a 55%,#e2e2e2)"></div>
    <h3 style="left:857px">LOREM IPSUM IS SIMPLY</h3>
    <p style="left:857px">Lorem Ipsum is simply dummy text of the printing and typesetting industry. Lorem Ipsum has been the</p>
    <time style="left:857px">MAY 27, 2014</time>
    <a class="btn" href="#" style="left:857px">Read More</a>
  </article>
</section>

<section class="partners">
  <div class="badge" style="left:186px;border-radius:14px"></div>
  <div class="badge" style="left:359px;height:40px;top:72px;border-radius:20px"></div>
  <div class="badge" style="left:549px"></div>
  <div class="badge" style="left:738px;border-radius:10px"></div>
  <div class="badge" style="left:912px;height:44px;top:70px;width:104px;border-radius:6px"></div>
  <h3>LOREM IPSUM IS SIMPLY DUMMY TEXT OF THE PRINTING</h3>
  <div class="rule"></div>
  <p>Lorem Ipsum is simply dummy text of the printing and typesetting industry. Lorem Ipsum has been the industry's standard dummy text ever since the dummy text ever since the</p>
</section>

<section class="contact">
  <h2><svg width="36" height="40" viewBox="0 0 36 40"><circle cx="16" cy="10" r="9" fill="#fff"/><path d="M0 40 Q0 22 16 22 Q30 22 32 32 L32 40 Z" fill="#fff"/><path d="M24 33 h10 M29 28 v10" stroke="#0555a3" stroke-width="3"/></svg>CONTACT US</h2>
  <div class="field" style="top:108px">Name :</div>
  <div class="field" style="top:173px">E mail :</div>
  <div class="field" style="top:238px">Phone :</div>
  <div class="field message">Message :</div>
  <p class="note">If you would like to contact us directly please feel free to Email us at Hello@TRELVOXstudio.example</p>
</section>

<footer class="site-footer">
  <div class="col" style="left:141px"><h4>ABOUT US</h4><ul><li>Eco-Friendly Flowers</li><li>Chief Floral Designer</li><li>About the Team</li><li>Blog</li><li>Press</li><li>Privacy &amp; Legal Stuff</li></ul></div>
  <div class="col" style="left:336px"><h4>WORKING WITH US</h4><ul><li>Affiliates</li><li>For Florists</li><li>Referral Program</li><li>Contact Us</li></ul></div>
  <div class="col" style="left:545px"><h4>FOR MEMBERS</h4><ul><li>Gift Cards</li><li>Bulk Orders / Events</li><li>For Businesses</li><li>For Florists</li></ul></div>
  <div class="col" style="left:729px;width:160px"><h4>CUSTOMER CARE</h4><ul><li>FAQ's about Petalworks Flowers</li><li>Customer Service</li><li>Replacement &amp; Refund Policy</li><li>Flower Care</li></ul></div>
  <div class="col follow" style="left:937px"><h4>FOLLOW US</h4><ul><li><span></span>Circlefeed</li><li><span></span>Chirpline</li><li><span></span>Linkwork</li></ul></div>
</footer>
<div class="bottombar">
  <div class="mark">TRELVOX</div>
  <div class="links">Home &nbsp;|&nbsp; About us &nbsp;|&nbsp; Services &nbsp;|&nbsp; News &nbsp;|&nbsp; Contact us</div>
  <div class="copy">Copyrights@trelvoxstudio.2014 All rights reserved</div>
</div>

</body>
</html>
```